Business card design needed to incorporate existing logo

We need a business card for a new modern Accounting & Business Solutions company call TelmaNord Partners.com.au servicing all of Australia.
My tagline is Steady Ledger Answers... that deliver.

We specialise in Cloud Accounting and this is our primary focus. We also provide tax representation, debt recovery, computer, tablet and smart phone sales.

I would like a design that uses my corporate, trustworthy colours of blue/white, black/grey however am open to suggestion. I have attached my logo to go on the card somewhere,of which you will see the colour scheme.

I am after a card that STANDS OUT, somewhere between it not being too busy and not being a baron waste of space.

A 'cloud' incorporated in the design may work well, up to your artistic judgement. I know what I like when I see it; it is harder to put into words!

Excited to see your ideas!
I have added my logo predominately (blue/white) and for additional opportunity have added my reverse logo (darker one). I have used the blue/white on my website and letterhead. I will be using both on my vehicle signage.

Target Market(s)

Tradesmen and small-medium businesses of all descriptions Australia-wide

Industry/Entity Type

Debt

Contact Information for Business Card

Doug Hallett
Principal (optional)
TelmaNord Partners.com.au
Steady Ledger Answers... that deliver

P: 1800 493 518
M: 0412 658 071 (optional)
W: www.telmanordpartners.com.au
E: admin@telmanordpartners.com.au

Logo Text

Steady Ledger Answers... that deliver!

Logo styles of interest
Wordmark Logo
Requirements
Must have
• Must look professional and of high quality not cheap.

My logo and my tagline 'Steady Ledger Answers... that deliver'.

I have my colourscheme in mind as per my attached logo, however am open to suggestion. I want to see what you can create that I would not have thought of.

Modern, innovative.
Something I won't look at and think, 'I could have done that myself'.

Must be able to be printed on Prinvo 300gm premium cards and the artwork provided to me.
Nice to have
• Title of Principal is optional depending on space and judement call of look/fee.
M: (mobile) number is also optional as above.

Somthing cloud related given the Cloud Accounting aspect may be relevant. I leave it to your artistic design and judgement.
Should not have
• Must not look cheap.

```html
<!DOCTYPE html>
<html lang="en">
<head>
<meta charset="utf-8">
<title>TelmaNord Partners – Business Card</title>
<link rel="stylesheet" href="https://fonts.googleapis.com/css2?family=Jost:wght@300;500;600;700&display=swap">
<style>
  :root {
    --backdrop: #d8d5d1;
    --navy: #232c5e;
    --navy-light: #34407a;
    --navy-dark: #1b2350;
    --paper: #f4f4f6;
    --paper-edge: #e3e3e7;
    --plum: #4a2a6c;
    --white: #ffffff;
  }
  * { margin: 0; padding: 0; box-sizing: border-box; }
  html, body {
    width: 1200px; height: 1181px; overflow: hidden;
    background: var(--backdrop);
    font-family: "Jost", "Century Gothic", sans-serif;
  }
  .canvas { position: relative; width: 1200px; height: 1181px; }

  .card {
    position: absolute; left: 242px; width: 715px;
    border-radius: 28px; overflow: hidden;
    box-shadow: 0 6px 14px rgba(0,0,0,0.25);
  }

  /* Front */
  .card-front {
    top: 153px; height: 412px;
    background: radial-gradient(ellipse at 50% 30%, var(--navy-light) 0%, var(--navy) 55%, var(--navy-dark) 100%);
  }
  .wordmark {
    position: absolute; left: 0; right: 0; top: 318px;
    text-align: center; color: var(--white); font-weight: 300;
  }
  .card-front .wordmark { top: 165px; }
  .wordmark-name {
    display: block; font-size: 58px; line-height: 1; letter-spacing: 0.06em;
  }
  .wordmark-domain {
    display: block; margin-top: 12px; font-size: 21px; letter-spacing: 0.28em;
  }

  /* Back */
  .card-back {
    top: 607px; height: 411px;
    background: radial-gradient(ellipse at 50% 35%, var(--white) 0%, var(--paper) 50%, var(--paper-edge) 100%);
  }
  .band { position: absolute; left: 0; right: 0; }
  .band-top {
    top: 0; height: 50px;
    background: radial-gradient(ellipse at 50% 0%, var(--navy-light) 0%, var(--navy) 70%);
  }
  .band-bottom {
    bottom: 0; height: 50px; background: var(--navy);
    color: var(--white); font-size: 15px; font-weight: 500;
    display: flex; align-items: center; justify-content: center;
  }
  .emblem-faint { position: absolute; left: 513px; top: 130px; }

  .person { position: absolute; left: 0; right: 0; top: 177px; text-align: center; color: var(--plum); }
  .person-name { font-size: 27px; font-weight: 600; line-height: 1; }
  .person-title {
    margin-top: 6px; font-size: 14px; font-weight: 700;
    letter-spacing: 0.95em; padding-left: 0.95em;
  }

  .contacts {
    position: absolute; top: 310px; left: 0; right: 0;
    font-size: 11px; font-weight: 600; color: var(--plum); line-height: 14px;
  }
  .contacts-left { position: absolute; right: 368px; text-align: right; }
  .contacts-right { position: absolute; left: 370px; text-align: left; }
  .divider {
    position: absolute; left: 358px; top: -10px; width: 2px; height: 52px;
    background: linear-gradient(var(--paper), var(--plum), var(--paper));
  }
</style>
</head>
<body>
<main class="canvas">

  <section class="card card-front" aria-label="Card front">
    <div class="wordmark">
      <span class="wordmark-name">TELMANORD</span>
      <span class="wordmark-domain">PARTNERS.COM.AU</span>
    </div>
  </section>

  <section class="card card-back" aria-label="Card back">
    <div class="band band-top"></div>

    <svg class="emblem-faint" width="175" height="175" viewBox="0 0 175 175" role="img" aria-label="Faint brand circle">
      <defs>
        <radialGradient id="emblemFill" cx="40%" cy="60%" r="65%">
          <stop offset="0" stop-color="#eef0f6"/>
          <stop offset="1" stop-color="#d3d8e6"/>
        </radialGradient>
      </defs>
      <circle cx="87.5" cy="87.5" r="86" fill="url(#emblemFill)" opacity="0.85"/>
    </svg>

    <div class="person">
      <p class="person-name">Doug Hallett</p>
      <p class="person-title">Principal</p>
    </div>

    <div class="contacts">
      <div class="contacts-left">
        <p>M : 0412 658 071</p>
        <p>admin@telmanordpartners.com.au</p>
      </div>
      <div class="divider"></div>
      <div class="contacts-right">
        <p>P : 1800 493 518</p>
        <p>www.telmanordpartners.com.au</p>
      </div>
    </div>

    <div class="band band-bottom">Steady Ledger Answers... that deliver</div>
  </section>

</main>
</body>
</html>
```